Young Architect Bussiness Card

English is not my first language (spanish is).
Need a bussiness card design for my best friend who is about to graduate from college, Licentiate degree in architecture, so she needs business cards to start networking, currently she has no porfolio, web page or plazared. so she is relying on her cel phone and correovela, but should leave space for one of them (plazared)

Design for business card should be modern, maybe something with construction blue prints patern or 3D modelling.

Name: Mariela Otárola Bonilla
Licentiate in Arquitecture
Cel: (506) XXX-4827
email: marielaXXX@correovela.com

Services, although im not sure if it has to be there or not:
Anteproyectos / Proposal design
Inspecciones / Site Inspections
Modelado 3D / 3D modelling
Planos Constructivos / Construction Blue Prints
Presupuestos / Budgets

Design should be in spanish

Industry/Entity Type

Architect

Contact Information for Business Card

Name: Mariela Otárola, Arquitecto
Associtation code : XXXX
Phone: (506) XXXX-XXXX
Email: xxx@correovela.com
Plazared: xxxx

Requirements
Must have
• Design for business card should be modern, maybe something with construction blue prints patern or 3D modelling.
Nice to have
• Something like a transition from 2D to 3D.

```html
<!DOCTYPE html>
<html lang="es">
<head>
<meta charset="utf-8">
<title>Mariela Otárola Bonilla – Tarjeta de presentación</title>
<link rel="stylesheet" href="https://fonts.googleapis.com/css2?family=Open+Sans:wght@400;600;700&family=Arimo:wght@700&display=swap">
<style>
  :root {
    --backdrop: #a79e97;
    --card-white: #ffffff;
    --band-grey: #cdcdcd;
    --band-grey-dark: #bdbdbd;
    --ink: #1d1d1d;
    --ink-soft: #3a3a3a;
    --accent-red: #c8102e;
    --photo-yellow: #f0d36a;
    --photo-sky: #d3e5f1;
    --photo-blue: #a6c6dc;
  }
  * { margin: 0; padding: 0; box-sizing: border-box; }
  html, body { width: 1200px; height: 864px; overflow: hidden; }
  body {
    background: var(--backdrop);
    font-family: "Open Sans", sans-serif;
    position: relative;
  }
  .card {
    position: absolute;
    left: 240px;
    width: 720px;
    height: 405px;
    overflow: hidden;
    box-shadow: 0 6px 18px rgba(0,0,0,.22);
  }
  /* Front */
  .card--front { top: 18px; }
  .front__photo {
    position: absolute; inset: 0;
    background: linear-gradient(160deg, var(--photo-yellow) 0%, var(--photo-sky) 45%, var(--photo-blue) 100%);
  }
  .front__name {
    position: absolute;
    left: 250px; bottom: 60px;
    font-family: "Arimo", sans-serif;
    font-weight: 700;
    font-size: 40px;
    letter-spacing: 1px;
    color: var(--ink);
  }
  /* Back */
  .card--back { top: 441px; background: var(--card-white); }
  .back__sketch {
    position: absolute; right: 0; top: 0;
    width: 430px; height: 165px;
    background: linear-gradient(200deg, #eeeeee, #fafafa 60%, var(--card-white));
  }
  .back__band {
    position: absolute; left: 0; right: 0; top: 165px; bottom: 0;
    background: linear-gradient(180deg, var(--band-grey), var(--band-grey-dark));
  }
  .back__name {
    position: absolute; left: 60px; top: 62px;
    color: var(--accent-red);
    font-size: 31px; font-weight: 400;
  }
  .back__title {
    position: absolute; left: 60px; top: 104px;
    color: var(--ink);
    font-size: 17px; font-weight: 700;
  }
  .back__contact {
    position: absolute; left: 0; top: 184px; width: 100%;
    display: flex; font-size: 17px; color: var(--ink);
    line-height: 28px;
  }
  .contact__left { width: 392px; text-align: right; padding-right: 12px; border-right: 1.5px solid var(--ink-soft); }
  .contact__right { padding-left: 12px; }
  .back__services-title {
    position: absolute; left: 0; width: 100%; top: 248px;
    text-align: center; color: var(--accent-red);
    font-size: 22px; font-weight: 400;
  }
  .back__services {
    position: absolute; left: 0; width: 100%; top: 280px;
    list-style: none; text-align: center;
    font-size: 16px; line-height: 22px; color: var(--ink-soft);
  }
</style>
</head>
<body>
  <section class="card card--front">
    <div class="front__photo" role="img" aria-label="Fotografía de casco amarillo, regla y metro plegable sobre planos de construcción"></div>
    <p class="front__name">MARIELA OTÁROLA</p>
  </section>

  <section class="card card--back">
    <div class="back__sketch" role="img" aria-label="Dibujo técnico tenue de una casa en perspectiva con lápiz"></div>
    <div class="back__band"></div>
    <h1 class="back__name">Mariela Otárola Bonilla</h1>
    <p class="back__title">Licentiate in Arquitecture</p>
    <div class="back__contact">
      <div class="contact__left">
        <p>(506) XXX-4827</p>
        <p>Associtation code : XXXX</p>
      </div>
      <div class="contact__right">
        <p>marielaXXX@correovela.com</p>
        <p>Plazared: xxxx</p>
      </div>
    </div>
    <h2 class="back__services-title">Services</h2>
    <ul class="back__services">
      <li>Anteproyectos / Proposal design</li>
      <li>Inspecciones / Site Inspections</li>
      <li>Modelado 3D / 3D modelling</li>
      <li>Planos Constructivos / Construction Blue Prints</li>
      <li>Presupuestos / Budgets</li>
    </ul>
  </section>
</body>
</html>
```